WordPress webdesign with coding for our company BRISK The Answer

BRISK The Answer is a payrolling company such as Montaval Wages (one of our competitor https://www.montaval-wages.ch/fr/). We need to set up our website in both languages (Fr and Eng). Our logo is enclosed.
we would like something simple explaining what is payrolling in Graph and wording, who we are and a contact page. you can also take some example if needed from our mother company BRISK The Horizon (www.briskthehorizon.ch) or our sister company (www.briskyourstride.ch). we would like to keep the color panel of our logo (ref. Black = PANTONE P Process Black C
Pink = PANTONE P Process Magenta C
Grey = PANTONE 430 C) as the driver of the website.

```html
<!DOCTYPE html>
<html lang="en">
<head>
<meta charset="utf-8">
<title>BRISK The Answer — Payrolling</title>
<link href="https://fonts.googleapis.com/css2?family=League+Spartan:wght@300;400;500;600;700&display=swap" rel="stylesheet">
<style>
:root{
  --magenta:#ec2a8e;
  --ink:#231f20;
  --dark:#2b2527;
  --grey:#7c878e;
  --light:#f4f4f5;
  --line:#cfd2d4;
  --white:#ffffff;
  --star:#f7c948;
}
*{box-sizing:border-box;margin:0;padding:0}
html,body{width:1200px;height:3070px;overflow:hidden}
body{position:relative;background:var(--white);color:var(--ink);font-family:"League Spartan",sans-serif}
.abs{position:absolute}
.pink{color:var(--magenta)}
.btn{position:absolute;background:var(--magenta);color:var(--white);font-size:17px;font-weight:500;text-transform:uppercase;display:flex;align-items:center;justify-content:center;letter-spacing:.2px}
.rule{display:inline-block;width:44px;height:2px;background:var(--magenta);vertical-align:middle;margin-left:18px}
.rule.before{margin:0 18px 0 0}
.section-title{font-size:33px;font-weight:600;letter-spacing:-.3px;text-transform:uppercase}
.section-sub{font-size:18px;font-weight:400;color:var(--magenta);text-transform:uppercase;line-height:33px}
.body-text{font-size:17px;line-height:34.5px;font-weight:400}

/* header */
.site-header{left:0;top:0;width:1200px;height:80px;background:var(--white)}
.brand{left:111px;top:18px}
.brand-name{font-size:44px;font-weight:500;line-height:40px;letter-spacing:1px;color:var(--ink)}
.brand-tag{font-size:10px;letter-spacing:7.5px;color:var(--ink);margin-top:2px}
.main-nav{top:36px;left:504px;display:flex;gap:37px;font-size:14.5px;text-transform:uppercase}
.main-nav .current{color:var(--magenta)}
.lang{top:36px;left:1039px;font-size:14.5px}

/* hero */
.hero{left:0;top:80px;width:1200px;height:451px;background:linear-gradient(90deg,#4a4442 0%,#b9b6b4 28%,#e9e7e6 55%,#f4f1f2 80%,#eddce4 100%)}
.hero-title{right:111px;top:176px;font-size:34px;font-weight:500;letter-spacing:-.3px}
.hero-text{right:111px;top:243px;width:520px;text-align:right;font-size:17px;line-height:35px}

/* callback */
.callback{left:679px;top:472px;width:410px;height:556px;background:var(--white);box-shadow:0 2px 12px rgba(0,0,0,.12)}
.callback h2{position:absolute;top:32px;width:100%;text-align:center;font-size:26px;font-weight:500}
.field{position:absolute;left:25px;width:360px;height:44px;border:1px solid #a9adb1;display:flex;align-items:center;padding-left:20px;font-size:13.5px;text-transform:uppercase;color:#2f3a57}
.field svg{margin-right:18px}
.field.msg{height:81px;align-items:flex-start;padding-top:14px}

/* who */
.who-text{left:111px;top:713px;width:490px}

/* payrolling */
.pay-band{left:298px;top:1113px;width:902px;height:484px;background:var(--dark)}
.pay-visual{left:111px;top:1164px;width:467px;height:382px;border-radius:20px;background:linear-gradient(160deg,#1d3a4c 0%,#0f2433 55%,#2a4250 100%);box-shadow:0 0 22px rgba(236,42,142,.45);overflow:hidden}
.pay-copy{left:647px;top:1168px;width:440px;color:var(--white)}

/* services */
.card{position:absolute;top:1805px;width:309px;height:336px;background:var(--white);border-radius:12px;box-shadow:0 1px 8px rgba(0,0,0,.13);padding:34px 24px 0 30px}
.card.active{border:1px solid #f3a9cf}
.card h3{font-size:20px;font-weight:500;line-height:33px;text-transform:uppercase;margin-top:26px;margin-bottom:12px}
.card p{font-size:16px;line-height:33.5px;color:#4a4a4a}

/* testimonials */
.testi-band{left:0;top:2317px;width:898px;height:407px;background:var(--dark)}
.testi-copy{left:110px;top:2392px;width:420px;color:var(--white)}
.testi-card{left:618px;top:2368px;width:468px;height:305px;background:var(--white);border-radius:22px;box-shadow:0 0 18px rgba(236,42,142,.35);padding:28px 36px 0}
.testi-card blockquote{font-size:16.5px;line-height:34.5px;color:#3a3a3a;margin-top:10px}
.author{font-size:16.5px;margin-top:12px;font-weight:500}
.dots{position:absolute;right:26px;bottom:26px;display:flex;gap:8px}
.dots i{width:5px;height:5px;border-radius:50%;border:1px solid var(--magenta)}
.dots i.on{background:var(--magenta)}

/* footer */
.footer-col{position:absolute;top:2806px}
.footer-col h4{font-size:18px;font-weight:500;color:var(--magenta);text-transform:uppercase;margin-bottom:16px}
.footer-col a{display:block;font-size:14.5px;text-transform:uppercase;line-height:36px;color:var(--ink);text-decoration:none}
.footer-rule{left:107px;top:3014px;width:986px;height:1px;background:var(--line)}
.copyright{left:0;top:3035px;width:1200px;text-align:center;font-size:14.5px;text-transform:uppercase}
</style>
</head>
<body>

<header class="abs site-header">
  <div class="abs brand"><div class="brand-name">BRISK</div><div class="brand-tag">THE ANSWER</div></div>
  <nav class="abs main-nav"><span class="current">Home</span><span>What is payrolling</span><span>About us</span><span>Contact</span></nav>
  <div class="abs lang">FR / <span class="pink">EN</span></div>
</header>

<section class="abs hero" role="img" aria-label="Photo of a businesswoman at a desk reviewing payroll documents"></section>
<h1 class="abs hero-title">YOUR <span class="pink">PAYROLL</span>. OUR <span class="pink">EXPERTISE</span></h1>
<p class="abs hero-text">Flexible, transparent, and secure payrolling solutions backed by the BRISK Group.</p>
<a class="btn" style="left:945px;top:341px;width:144px;height:43px">Start today</a>

<form class="abs callback">
  <h2>REQUEST A <span class="pink">CALL</span> BACK</h2>
  <div class="field" style="top:89px"><svg width="10" height="11" viewBox="0 0 10 11"><circle cx="5" cy="3" r="2.6" fill="#333"/><path d="M0 11c0-4 10-4 10 0z" fill="#333"/></svg>Full name</div>
  <div class="field" style="top:157px"><svg width="12" height="9" viewBox="0 0 12 9"><rect width="12" height="9" fill="#333"/><path d="M0 0l6 5 6-5" stroke="#fff" fill="none"/></svg>Email address</div>
  <div class="field" style="top:226px"><svg width="10" height="11" viewBox="0 0 10 11"><rect x="1" y="0" width="5" height="11" fill="#333"/><rect x="6" y="4" width="3" height="7" fill="#333"/></svg>Company name</div>
  <div class="field" style="top:294px"><svg width="11" height="11" viewBox="0 0 11 11"><path d="M2 0l2 3-1 1.5c1 2 2 3 3.5 3.5L8 7l3 2-1.5 2C5 11 0 6 0 1.5z" fill="#333"/></svg>Phone number</div>
  <div class="field msg" style="top:364px"><svg width="11" height="10" viewBox="0 0 11 10"><ellipse cx="5.5" cy="4.3" rx="5.5" ry="4.3" fill="#333"/><path d="M2 7l-1 3 4-2z" fill="#333"/></svg>Message</div>
  <a class="btn" style="left:25px;top:470px;width:360px;height:44px">Send message now</a>
</form>

<section>
  <h2 class="abs section-title" style="left:111px;top:608px">Who we are<span class="rule"></span></h2>
  <p class="abs section-sub" style="left:111px;top:668px">Your trusted partner in payroll solutions</p>
  <p class="abs body-text who-text">BRISK The Answer is more than a payroll provider — we’re your strategic partner in ensuring your employees are paid accurately, on time, and in full compliance with local regulations. Part of the BRISK Group, we combine the reliability of decades of experience with the agility of a modern service provider. We manage salaries, taxes, and compliance so you can focus on growth and your people.</p>
  <a class="btn" style="left:111px;top:987px;width:144px;height:42px">Learn more</a>
</section>

<section>
  <div class="abs pay-band"></div>
  <div class="abs pay-visual" role="img" aria-label="Photo of a tablet displaying a rising line chart">
    <svg width="467" height="382" viewBox="0 0 467 382">
      <g stroke="#3e6b80" stroke-width="1" opacity=".6">
        <line x1="40" y1="52" x2="420" y2="52"/><line x1="40" y1="90" x2="420" y2="90"/><line x1="40" y1="128" x2="420" y2="128"/><line x1="40" y1="166" x2="420" y2="166"/><line x1="40" y1="204" x2="420" y2="204"/><line x1="40" y1="242" x2="420" y2="242"/>
      </g>
      <line x1="40" y1="242" x2="450" y2="242" stroke="#8fb3c2" stroke-width="2"/>
      <polyline points="45,240 90,200 140,200 175,165 210,150 250,135 290,100 320,110 355,70 390,65 425,50" fill="none" stroke="#38a9e6" stroke-width="3"/>
      <polyline points="45,240 110,180 150,170 175,190 200,130 230,160 270,120 310,95 355,105 390,85 425,75" fill="none" stroke="#f39b25" stroke-width="3"/>
      <polyline points="45,240 100,210 135,190 170,180 200,190 240,175 265,160 295,190 330,150 380,120 425,95" fill="none" stroke="#8fd34a" stroke-width="3"/>
    </svg>
  </div>
  <div class="abs pay-copy">
    <h2 class="section-title" style="text-transform:none">WHAT IS PAYROLLING?<span class="rule"></span></h2>
    <p class="section-sub" style="margin-top:24px">Your partner for stress-free payroll management</p>
    <p class="body-text" style="margin-top:12px">Payrolling is a flexible HR solution that allows companies to hire and manage employees without handling payroll administration internally. We take care of salaries, social charges, insurance, and compliance so you can focus.</p>
  </div>
  <a class="btn" style="left:648px;top:1486px;width:144px;height:43px">Learn more</a>
</section>

<section>
  <h2 class="abs section-title" style="left:0;width:1200px;text-align:center;top:1673px"><span class="rule before"></span>Our services<span class="rule"></span></h2>
  <p class="abs section-sub" style="left:0;width:1200px;text-align:center;top:1729px">Flexible payroll solutions tailored to your needs</p>

  <article class="card" style="left:111px">
    <svg width="68" height="62" viewBox="0 0 68 62" fill="none" stroke="#ec2a8e" stroke-width="2"><rect x="2" y="2" width="40" height="56"/><circle cx="18" cy="18" r="6"/><line x1="8" y1="34" x2="34" y2="34"/><line x1="8" y1="42" x2="30" y2="42"/><rect x="36" y="24" width="20" height="34" transform="rotate(-15 46 41)"/><circle cx="48" cy="42" r="5"/></svg>
    <h3>Payroll management</h3>
    <p>We manage salaries, social contributions, insurance, and taxes with complete accuracy and compliance.</p>
  </article>
  <article class="card active" style="left:444px">
    <svg width="68" height="62" viewBox="0 0 68 62" fill="none" stroke="#ec2a8e" stroke-width="2"><rect x="16" y="2" width="34" height="38"/><line x1="22" y1="10" x2="44" y2="10"/><line x1="22" y1="18" x2="44" y2="18"/><line x1="22" y1="26" x2="44" y2="26"/><circle cx="33" cy="46" r="6"/><circle cx="8" cy="44" r="4"/><path d="M2 60v-8h12v8"/><circle cx="58" cy="44" r="4"/><path d="M52 60v-8h12v8"/></svg>
    <h3>Employment<br>outsourcing</h3>
    <p>We become the legal employer for your staff while you keep full operational control.</p>
  </article>
  <article class="card" style="left:778px">
    <svg width="68" height="62" viewBox="0 0 68 62" fill="none" stroke="#ec2a8e" stroke-width="2"><rect x="10" y="12" width="36" height="46"/><line x1="18" y1="24" x2="38" y2="24"/><line x1="18" y1="32" x2="38" y2="32"/><path d="M50 2l12 5v10c0 8-6 13-12 15-6-2-12-7-12-15V7z"/><path d="M44 16l5 5 8-9"/><rect x="2" y="40" width="16" height="14"/><path d="M5 40v-5a5 5 0 0110 0v5"/></svg>
    <h3>Compliance &amp; risk<br>management</h3>
    <p>Stay fully compliant with Swiss regulations — we handle risks, updates, and reporting.</p>
  </article>
  <a class="btn" style="left:496px;top:2189px;width:208px;height:43px;font-size:16px">View more services</a>
</section>

<section>
  <div class="abs testi-band"></div>
  <div class="abs testi-copy">
    <h2 class="section-title" style="text-transform:uppercase">Testimonials<span class="rule"></span></h2>
    <p class="section-sub" style="margin-top:24px">What our clients says</p>
    <p class="body-text" style="margin-top:16px">Working with BRISK The Answer has been a game-changer for our company. Their team handles payroll and compliance with absolute professionalism, giving us the freedom to focus on growth.</p>
  </div>
  <div class="abs testi-card">
    <svg width="140" height="22" viewBox="0 0 140 22" fill="#f7c948">
      <g id="s"><path d="M11 0l3 7.5 8 .5-6 5 2 8-7-4.5-7 4.5 2-8-6-5 8-.5z"/></g>
      <use href="#s" x="28"/><use href="#s" x="56"/><use href="#s" x="84"/><use href="#s" x="112"/>
    </svg>
    <blockquote>"BRISK The Answer completely transformed the way we manage our external workforce. Before working with them, our HR team was drowning in paperwork and struggling to keep up with compliance rules...</blockquote>
    <p class="author"><span class="pink" style="font-weight:400">MARGOT D.,</span> HR DIRECTOR, GENEVA</p>
    <div class="dots"><i class="on"></i><i></i><i></i><i></i></div>
  </div>
</section>

<footer>
  <div class="abs brand" style="top:2808px;left:113px"><div class="brand-name">BRISK</div><div class="brand-tag">THE ANSWER</div></div>
  <div class="footer-col" style="left:399px"><h4>Quick links</h4><a>Home</a><a>What is payrolling</a><a>About us</a><a>Contact</a></div>
  <div class="footer-col" style="left:685px"><h4>Resources</h4><a>FAQs</a><a>Blog / Articles</a><a>Testimonials</a></div>
  <div class="footer-col" style="left:937px"><h4>Support</h4><a>Contact</a><a>Privacy policy</a><a>Terms &amp; conditions</a></div>
  <div class="abs footer-rule"></div>
  <p class="abs copyright">© 2025 <span class="pink">BRISK The Answer</span>. All rights reserved.</p>
</footer>

</body>
</html>
```